MRT Property - Business Cards

Looking for a business card & general letterhead, signage etc design for our new logo.

Colours:
000a20
0056a2
00b5ef
0088ce
68cef2

Fonts:
Poppins
Karla

Please keep look and feel of new brand - example in the zip package I sent.

```html
<!DOCTYPE html>
<html lang="en">
<head>
<meta charset="utf-8">
<title>MRT Property – Business Cards</title>
<link href="https://fonts.googleapis.com/css2?family=Montserrat:wght@400;500;600&family=Caveat:wght@500&display=swap" rel="stylesheet">
<style>
  :root {
    --backdrop: #9b9b9b;
    --navy: #121628;
    --brand-blue: #0056a2;
    --accent-blue: #0088ce;
    --sky: #00b5ef;
    --ink: #1b1b1b;
    --paper: #ffffff;
  }
  * { margin: 0; padding: 0; box-sizing: border-box; }
  html, body { width: 1093px; height: 1200px; overflow: hidden; }
  body {
    background: var(--backdrop);
    position: relative;
    font-family: "Montserrat", sans-serif;
  }
  .card {
    position: absolute;
    left: 264px;
    width: 582px;
    height: 364px;
    border-radius: 18px;
    overflow: hidden;
    background: var(--navy);
  }
  .card--front { top: 225px; }
  .card--back { top: 616px; height: 366px; }

  .front-shape { position: absolute; inset: 0; }

  .wordmark {
    position: absolute;
    display: flex;
    align-items: center;
    font-family: "Montserrat", sans-serif;
    font-weight: 600;
    white-space: nowrap;
  }
  .wordmark__dot { border-radius: 50%; flex: none; }
  .card--front .wordmark {
    left: 38px; top: 152px; font-size: 25px; color: var(--brand-blue); gap: 10px;
  }
  .card--front .wordmark__dot { width: 22px; height: 22px; background: var(--accent-blue); }
  .card--back .wordmark {
    left: 0; right: 0; top: 158px; justify-content: center;
    font-size: 48px; color: var(--paper); gap: 18px;
  }
  .card--back .wordmark__dot { width: 40px; height: 40px; background: var(--accent-blue); }

  .divider {
    position: absolute; left: 278px; top: 84px; width: 2px; height: 175px;
    background: var(--brand-blue);
  }
  .details { position: absolute; left: 289px; top: 80px; color: var(--ink); }
  .details__name {
    font-family: "Caveat", cursive;
    font-weight: 500;
    font-size: 33px;
    line-height: 1;
    color: var(--brand-blue);
  }
  .details__role { font-size: 13px; margin-top: 1px; }
  .details__address { font-size: 13px; line-height: 18px; margin-top: 14px; }
  .contact { list-style: none; margin-top: 15px; }
  .contact__item {
    display: flex; align-items: center; gap: 9px;
    font-size: 13px; height: 23px;
  }
  .contact__icon { width: 14px; height: 14px; fill: var(--brand-blue); flex: none; }
</style>
</head>
<body>
  <section class="card card--front" aria-label="Business card front">
    <svg class="front-shape" viewBox="0 0 582 364" width="582" height="364" aria-hidden="true">
      <path d="M0 0 H582 V281 Q291 331 0 281 Z" fill="var(--paper)"/>
      <path d="M39 283 Q291 322 542 283" fill="none" stroke="var(--brand-blue)" stroke-width="2.2"/>
    </svg>

    <div class="wordmark"><span class="wordmark__dot"></span>MRT Property</div>

    <div class="divider"></div>

    <div class="details">
      <h1 class="details__name">Daniel Hart</h1>
      <p class="details__role">Managing Director</p>
      <p class="details__address">480 Maple Ridge Ave Suite<br>210 Lakewood Ohio 44107</p>
      <ul class="contact">
        <li class="contact__item">
          <svg class="contact__icon" viewBox="0 0 24 24" aria-hidden="true"><path d="M6.6 10.8c1.4 2.8 3.8 5.1 6.6 6.6l2.2-2.2c.3-.3.7-.4 1-.2 1.1.4 2.3.6 3.6.6.6 0 1 .4 1 1V20c0 .6-.4 1-1 1C10.6 21 3 13.4 3 4c0-.6.4-1 1-1h3.5c.6 0 1 .4 1 1 0 1.3.2 2.5.6 3.6.1.3 0 .7-.2 1z"/></svg>
          <span>1 (530) 555-0142</span>
        </li>
        <li class="contact__item">
          <svg class="contact__icon" viewBox="0 0 24 24" aria-hidden="true"><path d="M2 5h20v14H2z M2 5l10 7 10-7" fill="var(--brand-blue)"/><path d="M3 6l9 6.3L21 6" fill="none" stroke="#fff" stroke-width="1.6"/></svg>
          <span>info@mrtproperty.com</span>
        </li>
        <li class="contact__item">
          <svg class="contact__icon" viewBox="0 0 24 24" aria-hidden="true"><circle cx="12" cy="12" r="10"/><path d="M2 12h20M12 2c3 3 3 17 0 20M12 2c-3 3-3 17 0 20" fill="none" stroke="#fff" stroke-width="1.4"/></svg>
          <span>www.mrtproperty.com</span>
        </li>
      </ul>
    </div>
  </section>

  <section class="card card--back" aria-label="Business card back">
    <div class="wordmark"><span class="wordmark__dot"></span>MRT Property</div>
  </section>
</body>
</html>
```